Business card design for my company.
I would like the card's background colour to be black. You can also see our web site to get an idea of our brand. https://www.tmwhomecrafting.com.au/
- Name
- Email

```html
<!DOCTYPE html>
<html lang="en">
<head>
<meta charset="utf-8">
<title>TMW Home Crafting – Business Card</title>
<link rel="stylesheet" href="https://fonts.googleapis.com/css2?family=Open+Sans:wght@400;600;700&display=swap">
<style>
  :root {
    --stage: #2b2b2d;
    --card: #1d1d1e;
    --edge: #14a044;
    --green: #1aa34a;
    --white: #f4f4f4;
    --muted: #e6e6e6;
    --rule: #8a8a8a;
  }
  * { box-sizing: border-box; margin: 0; padding: 0; }
  html, body { width: 1200px; height: 1088px; overflow: hidden; }
  body {
    background: var(--stage);
    font-family: "Open Sans", Arial, sans-serif;
    display: flex;
    flex-direction: column;
    align-items: center;
    justify-content: center;
    gap: 60px;
  }
  .card {
    width: 640px;
    height: 366px;
    background: var(--card);
    border-bottom: 6px solid var(--edge);
    position: relative;
  }
  .brand {
    display: flex;
    align-items: center;
    gap: 10px;
    color: var(--white);
    font-weight: 700;
    text-transform: uppercase;
    letter-spacing: 0.06em;
    white-space: nowrap;
  }
  .brand-square {
    width: 14px; height: 14px;
    background: var(--green);
    flex: none;
  }
  .brand-zone {
    position: absolute;
    left: 0; top: 0;
    width: 330px; height: 360px;
    display: flex;
    align-items: center;
    justify-content: center;
  }
  .card-front .brand { font-size: 18px; }
  .divider {
    position: absolute;
    left: 330px; top: 70px;
    width: 1px; height: 226px;
    background: var(--rule);
  }
  .details {
    position: absolute;
    left: 362px; top: 74px;
    color: var(--muted);
    font-size: 15px;
    line-height: 1.35;
  }
  .name {
    color: var(--green);
    font-weight: 700;
    font-size: 19px;
    letter-spacing: 0.02em;
    text-transform: uppercase;
  }
  .role { margin-bottom: 16px; }
  .location { margin-bottom: 16px; }
  .contact-list { list-style: none; }
  .contact-list li { display: flex; align-items: center; gap: 8px; }
  .contact-list svg { width: 12px; height: 12px; fill: var(--green); flex: none; }
  .card-back { display: flex; align-items: center; justify-content: center; }
  .card-back .brand { font-size: 34px; gap: 16px; letter-spacing: 0.08em; }
  .card-back .brand-square { width: 24px; height: 24px; }
</style>
</head>
<body>
  <section class="card card-front" aria-label="Business card front">
    <div class="brand-zone">
      <div class="brand"><span class="brand-square"></span>TMW Home Crafting</div>
    </div>
    <div class="divider"></div>
    <div class="details">
      <p class="name">Marcus Hale</p>
      <p class="role">Managing Director</p>
      <p class="location">Hobart, Tasmania<br>Australia</p>
      <ul class="contact-list">
        <li><svg viewBox="0 0 12 12"><path d="M3 1l2 2-1 1.5a7 7 0 003.5 3.5L9 7l2 2-1.5 2A9 9 0 011 2.5z"/></svg>0400 555 018</li>
        <li><svg viewBox="0 0 12 12"><path d="M1 2h10v8H1z M1.5 2.5L6 6.5l4.5-4" /></svg>info@tmwhomecrafting.com.au</li>
        <li><svg viewBox="0 0 12 12"><circle cx="6" cy="6" r="5.5"/></svg>www.tmwhomecrafting.com.au</li>
      </ul>
    </div>
  </section>

  <section class="card card-back" aria-label="Business card back">
    <div class="brand"><span class="brand-square"></span>TMW Home Crafting</div>
  </section>
</body>
</html>
```